Meridale Partners Website

Meridale Partners (MP) provide Analytics & Enterprise Performance Management (EPM) advisory & consultancy services. We are passionate about data and making a difference for our clients by working in partnership with them, helping them on their journey to becoming an Meridale Partner. We deliver insights which give our clients a competitive edge and a much deeper understanding of their organisation.

We need a website which shows who we are, what we do and how we do it.

www.meridale-partners.example is our very basic website at the moment. We want to completely revamp it with a corporate look

```html
<!DOCTYPE html>
<html lang="en">
<head>
<meta charset="utf-8">
<title>Meridale Partners</title>
<link href="https://fonts.googleapis.com/css2?family=Inter:wght@400;500;600;700&display=swap" rel="stylesheet">
<style>
:root{
  --navy:#2b5570;
  --navy-dark:#22475e;
  --orange:#e8843c;
  --peach:#fdf1e8;
  --ink:#1f2a33;
  --muted:#4a5560;
  --line:#e6e9ec;
  --white:#ffffff;
}
*{box-sizing:border-box;margin:0;padding:0}
html,body{width:1200px;height:3450px;overflow:hidden;background:var(--white)}
body{font-family:"Inter",sans-serif;color:var(--ink)}
.page{position:relative;width:1200px;height:3450px;overflow:hidden}
.abs{position:absolute}

/* brand */
.brand{display:flex;align-items:center;gap:12px}
.brand-dot{width:44px;height:44px;border-radius:50%;background:var(--navy)}
.brand-name{font-weight:700;font-size:14px;line-height:16px;color:var(--navy);letter-spacing:.3px}

/* hero */
.hero-bg{left:0;top:0;width:600px;height:600px;background:linear-gradient(135deg,#fbeee4,#fdf5ef)}
.hero-photo{left:600px;top:0;width:600px;height:675px;border-bottom-left-radius:140px;background:linear-gradient(160deg,#c9c4b8,#8a7c6e 55%,#5d6a72)}
.nav{left:652px;top:15px;width:488px;height:45px;border:1px solid var(--navy);border-radius:6px;display:flex;align-items:center;justify-content:space-around;font-size:12.5px;color:var(--navy);background:rgba(255,255,255,.75)}
.nav span.active::before{content:"•";margin-right:6px}
.eyebrow{left:60px;top:234px;font-size:18px;font-weight:500;color:var(--navy);letter-spacing:.2px}
.hero-title{left:58px;top:262px;font-size:48px;font-weight:700;line-height:57px;color:var(--navy)}
.hero-title .accent{color:var(--orange)}
.btn{display:inline-flex;align-items:center;gap:8px;background:var(--orange);color:var(--white);font-size:13px;font-weight:600;border-radius:22px;padding:0 22px;height:40px;letter-spacing:.2px}
.btn svg{width:14px;height:14px}

/* about */
.about-art{left:60px;top:705px;width:535px;height:540px;border-radius:50%;background:radial-gradient(circle,#2b5570 0 44%,#f6e3d3 45% 62%,#fff 72%)}
.about-text{left:675px;top:780px;width:380px}
.section-title{font-size:34px;font-weight:700;line-height:41px;color:var(--ink)}
.about-text p{font-size:13.2px;line-height:21.5px;color:var(--muted);margin-top:14px}
.about-text .section-title+p{margin-top:28px}
.about-text .btn{margin-top:28px}

/* services */
.services-band{left:0;top:1275px;width:1080px;height:413px;background:var(--navy)}
.services-title{left:60px;top:1335px;font-size:34px;font-weight:700;color:var(--white)}
.service{width:345px;height:383px}
.service-photo{position:absolute;left:0;top:0;width:345px;height:345px;border-radius:36px 36px 0 36px}
.service-label{position:absolute;left:60px;top:308px;width:285px;height:75px;background:var(--white);border-radius:6px;box-shadow:0 6px 18px rgba(0,0,0,.1);display:flex;align-items:center;padding:0 18px;gap:12px;font-size:18px;font-weight:600;color:var(--ink)}
.service-icon{width:38px;height:38px;border-radius:6px;background:#fbe3d1}
.service-go{margin-left:auto;width:24px;height:24px;border-radius:50%;border:1px solid #c7ccd1;display:flex;align-items:center;justify-content:center}
.service-go.on{background:var(--orange);border-color:var(--orange)}
.service-go svg{width:12px;height:12px}

/* process */
.center-title{left:0;width:1200px;text-align:center}
.step{width:248px;height:248px;background:var(--white);border-radius:18px;box-shadow:0 4px 22px rgba(0,0,0,.08);display:flex;flex-direction:column;align-items:center}
.step-art{width:140px;height:120px;margin-top:28px;border-radius:14px}
.step-name{margin-top:28px;font-size:18px;font-weight:600;color:var(--ink)}

/* testimonial */
.quote-bg{left:218px;top:2332px;width:982px;height:390px;border-top-left-radius:60px;background:linear-gradient(90deg,#fdf0e6,#fff8f3)}
.quote-photo{left:105px;top:2384px;width:225px;height:270px;border-radius:24px;background:linear-gradient(160deg,#6f6458,#c7a687 60%,#8d7663)}
.quote-text{left:390px;top:2398px;width:620px}
.quote-text blockquote{font-size:19.5px;line-height:31px;color:var(--muted);margin-top:20px}
.quote-text cite{display:block;margin-top:26px;font-style:normal;font-size:11.5px;color:var(--muted)}
.quote-text cite b{color:var(--navy);font-weight:600}

/* clients */
.clients{left:60px;top:2780px;width:1080px;display:flex;justify-content:space-between;align-items:center;font-size:21px;font-weight:600;color:#4f6f96}

/* cta */
.cta{left:60px;top:2858px;width:1080px;height:262px;background:var(--navy);border-bottom-right-radius:110px;overflow:hidden}
.cta-dot{left:45px;top:95px;width:80px;height:80px;border-radius:50%;background:var(--orange)}
.cta-small-dot{left:10px;top:38px;width:9px;height:9px;border-radius:50%;background:var(--orange)}
.cta-title{left:74px;top:105px;font-size:34px;font-weight:600;line-height:41px;color:var(--white);letter-spacing:.3px}
.cta .btn{left:848px;top:114px;height:36px;font-size:12.5px;font-weight:500;padding:0 18px}

/* footer */
.foot-col h4{font-size:17px;font-weight:500;color:var(--navy);letter-spacing:.3px;margin-bottom:14px}
.foot-links a{display:block;font-size:11.5px;color:var(--muted);text-decoration:none;line-height:30px;letter-spacing:.3px}
.contact-row{display:flex;gap:10px;font-size:11.5px;line-height:17px;color:var(--muted);margin-bottom:26px}
.contact-row svg{width:15px;height:15px;flex:none;margin-top:1px}
.foot-col p.small{font-size:11.5px;line-height:18px;color:var(--muted)}
.email-field{margin-top:18px;width:285px;height:40px;border:1px solid #cfd5da;border-radius:20px;display:flex;align-items:center;justify-content:space-between;padding:0 16px 0 22px;font-size:11.5px;color:var(--muted)}
.social{display:flex;gap:10px}
.social span{width:34px;height:34px;border-radius:50%;background:var(--orange)}
.social span+span{background:#fbe3d1}
.rule{left:60px;top:3400px;width:1080px;height:1px;background:var(--line)}
.copy{left:0;top:3420px;width:1200px;text-align:center;font-size:11.5px;color:var(--muted)}
.copy b{color:var(--navy);font-weight:600}
</style>
</head>
<body>
<div class="page">

  <!-- Hero -->
  <div class="abs hero-bg"></div>
  <div class="abs hero-photo" role="img" aria-label="Photo of a team working together at a whiteboard"></div>
  <div class="abs brand" style="left:60px;top:16px">
    <span class="brand-dot"></span>
    <span class="brand-name">MERIDALE<br>PARTNERS</span>
  </div>
  <nav class="abs nav">
    <span class="active">Home</span><span>About</span><span>Services</span><span>How We Do It</span><span>Contact</span>
  </nav>
  <div class="abs eyebrow">MERIDALE PARTNERS</div>
  <h1 class="abs hero-title"><span class="accent">Making A Difference</span><br>For Our Clients</h1>
  <a class="abs btn" style="left:60px;top:397px">GET STARTED
    <svg viewBox="0 0 14 14" fill="none" stroke="#fff" stroke-width="1.5"><path d="M2 7h10M8 3l4 4-4 4"/></svg></a>

  <!-- About -->
  <div class="abs about-art" role="img" aria-label="Photo of two colleagues reviewing a tablet, framed by a navy ring and dotted pattern"></div>
  <div class="abs about-text">
    <h2 class="section-title">About<br>Meridale Partners</h2>
    <p>MP are a Data Analytics &amp; EPM company, specialising in the implementation and support of Business Intelligence, EPM and Data Analytics business solutions, both in the Cloud and on-premise.</p>
    <p>Meridale Partners is an exciting start-up in the Data Analytics and EPM space. Founded in 2019, MP specialise in the implementation and support of BI, EPM and Data Analytics business solutions, both in the Cloud and on-premise.</p>
    <a class="btn">READ MORE
      <svg viewBox="0 0 14 14" fill="none" stroke="#fff" stroke-width="1.5"><path d="M2 7h10M8 3l4 4-4 4"/></svg></a>
  </div>

  <!-- Services -->
  <div class="abs services-band"></div>
  <h2 class="abs services-title">Our Services</h2>

  <div class="abs service" style="left:60px;top:1398px">
    <div class="service-photo" role="img" aria-label="Photo of a laptop showing analytics charts" style="background:linear-gradient(150deg,#7e8a6a,#d8c9b4 55%,#f1ece6)"></div>
    <div class="service-label"><span class="service-icon" role="img" aria-label="Analytics icon"></span>Analytics
      <span class="service-go"><svg viewBox="0 0 12 12" fill="none" stroke="#6b7580" stroke-width="1.3"><path d="M2 6h8M7 3l3 3-3 3"/></svg></span></div>
  </div>
  <div class="abs service" style="left:427px;top:1398px">
    <div class="service-photo" role="img" aria-label="Photo of an advisory meeting in an office" style="background:linear-gradient(150deg,#2f3330,#6a5d4c 55%,#a9a49a)"></div>
    <div class="service-label"><span class="service-icon" role="img" aria-label="EPM advisory icon"></span>EPM Advisory
      <span class="service-go on"><svg viewBox="0 0 12 12" fill="none" stroke="#fff" stroke-width="1.3"><path d="M2 6h8M7 3l3 3-3 3"/></svg></span></div>
  </div>
  <div class="abs service" style="left:795px;top:1398px">
    <div class="service-photo" role="img" aria-label="Photo of two consultants working at a laptop" style="background:linear-gradient(150deg,#4b5356,#2e3336 55%,#8c8680)"></div>
    <div class="service-label"><span class="service-icon" role="img" aria-label="Consultancy icon"></span>Consultancy
      <span class="service-go"><svg viewBox="0 0 12 12" fill="none" stroke="#6b7580" stroke-width="1.3"><path d="M2 6h8M7 3l3 3-3 3"/></svg></span></div>
  </div>

  <!-- How we do it -->
  <h2 class="abs section-title center-title" style="top:1848px">How We Do It</h2>
  <div class="abs step" style="left:165px;top:1927px">
    <div class="step-art" role="img" aria-label="Illustration of an advisor with a speech bubble" style="background:linear-gradient(135deg,#f3dcc6,#cfe0f0)"></div>
    <div class="step-name">Advise &amp; Architect</div>
  </div>
  <div class="abs step" style="left:476px;top:1912px">
    <div class="step-art" role="img" aria-label="Illustration of a light bulb and a gear" style="background:linear-gradient(135deg,#fbe6a6,#cdd6de)"></div>
    <div class="step-name">Design &amp; Implement</div>
  </div>
  <div class="abs step" style="left:787px;top:1927px">
    <div class="step-art" role="img" aria-label="Illustration of three coloured gears" style="background:linear-gradient(135deg,#f6c9c4,#c4ecd8,#c3e6f3)"></div>
    <div class="step-name" style="margin-top:42px">Optimise &amp; Manage</div>
  </div>
  <svg class="abs" style="left:380px;top:2010px" width="125" height="50" viewBox="0 0 125 50" fill="none" stroke="#1f2a33" stroke-width="1.4">
    <circle cx="6" cy="47" r="3" fill="#1f2a33"/>
    <path d="M8 46c30 8 34-20 52-26s30 6 40 22"/><path d="M93 38l7 5 2-8"/>
  </svg>
  <svg class="abs" style="left:697px;top:2010px" width="125" height="50" viewBox="0 0 125 50" fill="none" stroke="#1f2a33" stroke-width="1.4">
    <circle cx="4" cy="17" r="3" fill="#1f2a33"/>
    <path d="M6 17c22-8 30 4 38 16s22 14 36-4 24-14 32-11"/><path d="M104 13l8 5-7 5"/>
  </svg>

  <!-- Testimonial -->
  <h2 class="abs section-title center-title" style="top:2265px">What Clients Say</h2>
  <div class="abs quote-bg"></div>
  <div class="abs quote-photo" role="img" aria-label="Portrait photo of the client holding a clipboard"></div>
  <div class="abs quote-text">
    <svg width="38" height="30" viewBox="0 0 38 30" fill="#2b5570"><path d="M0 30V17C0 7 5 1 15 0v6c-5 1-7 4-7 9h7v15zM21 30V17c0-10 5-16 15-17v6c-5 1-7 4-7 9h7v15z"/></svg>
    <blockquote>Lorem ipsum dolor sit amet, consectetuer adipiscing elit, sed diam nonummy nibh euismod tincidunt ut laoreet dolore magna aliquam erat volutpat. Ut wisi enim ad minim veniam, quis nostrud exerci tation ullamcorper suscipit lobortis nisl ut aliquip ex ea commodo consequat.</blockquote>
    <cite><b>Nora Halloway</b>, Managing Director</cite>
  </div>

  <!-- Clients -->
  <div class="abs clients">
    <span>Northvale</span><span>Corvane</span><span>Tessly</span><span>Brightmoor</span><span>Quillford</span><span>Halvern</span>
  </div>

  <!-- CTA -->
  <div class="abs cta">
    <span class="abs cta-small-dot"></span>
    <span class="abs cta-dot"></span>
    <h2 class="abs cta-title">CONTACT US TO DISCUSS YOUR<br>BUSINESS NEEDS</h2>
    <a class="abs btn">
      <svg viewBox="0 0 14 14" fill="none" stroke="#fff" stroke-width="1.2"><path d="M3 1.5l2 .5 1 3-1.5 1a7 7 0 0 0 3.5 3.5l1-1.5 3 1 .5 2c-1 1.5-2.5 1.5-4 1A11 11 0 0 1 1.5 5.5C1 4 1 2.5 3 1.5z"/></svg>
      CONTACT US</a>
  </div>

  <!-- Footer -->
  <div class="abs brand" style="left:60px;top:3180px">
    <span class="brand-dot"></span>
    <span class="brand-name">MERIDALE<br>PARTNERS</span>
  </div>
  <div class="abs social" style="left:104px;top:3254px" aria-label="Social links"><span></span><span></span></div>

  <div class="abs foot-col" style="left:317px;top:3178px">
    <h4>QUICK LINKS</h4>
    <nav class="foot-links"><a>HOME</a><a>ABOUT</a><a>SERVICES</a><a>HOW WE DO IT</a><a>CONTACT</a></nav>
  </div>
  <div class="abs foot-col" style="left:534px;top:3178px">
    <h4>CONTACT DETAILS</h4>
    <div class="contact-row"><svg viewBox="0 0 15 15" fill="none" stroke="#e8843c" stroke-width="1.2"><path d="M7.5 14s5-4.5 5-8.5a5 5 0 0 0-10 0c0 4 5 8.5 5 8.5z"/><circle cx="7.5" cy="5.5" r="1.8"/></svg>
      <span>14 Harbour Row, Quayside,<br>Dublin 4, D04 KX21</span></div>
    <div class="contact-row"><svg viewBox="0 0 15 15" fill="none" stroke="#e8843c" stroke-width="1.2"><path d="M3.5 1.5l2 .5 1 3-1.5 1a7 7 0 0 0 3.5 3.5l1-1.5 3 1 .5 2c-1 1.5-2.5 1.5-4 1A11 11 0 0 1 2 6C1.5 4.5 1.5 3 3.5 1.5z"/></svg>
      <span style="font-weight:600">01 555 0142</span></div>
    <div class="contact-row"><svg viewBox="0 0 15 15" fill="none" stroke="#e8843c" stroke-width="1.2"><rect x="1.5" y="3" width="12" height="9" rx="1"/><path d="M1.5 4l6 4.5 6-4.5"/></svg>
      <span>hello@meridale-partners.example</span></div>
  </div>
  <div class="abs foot-col" style="left:854px;top:3178px">
    <h4>NEWSLETTER</h4>
    <p class="small">Subscribe to our newletter to get latest news &amp;<br>Updates</p>
    <div class="email-field">Email Address
      <svg width="18" height="18" viewBox="0 0 18 18" fill="none" stroke="#e8843c" stroke-width="1.3"><path d="M16 2L2 8l6 2 2 6z"/><path d="M16 2L8 10"/></svg></div>
  </div>

  <div class="abs rule"></div>
  <div class="abs copy">© <b>MERIDALE PARTNERS</b> - 2022. All Rights Reserved.</div>
</div>
</body>
</html>
```